Larkspur Talent IT Recruiting firm needs a business card design for Recruiters, Sourcers, and Account

We need business cards that allow us to change all contact info, names, titles (Recruiter, Sourcer, Account Manager, Director, CEO, etc) per person since we have three offices, in three cities, Phoenix, Austin, and Las Vegas. We do recruiting and contractors for IT positions (Developers, Architects, Software Engineers, Security Engineers, Help Desk, DBAs, PMs, Scrum Masters, etc.) Our client companies are very diverse from Meridian 100 to silicone Valley type start-ups.

So, while we what hip, techie, and quirky, it still needs to be professional. Primary color we use is blue, with silver as a secondary color.

Target Market(s)

IT, Technology

Industry/Entity Type

Business

Contact Information for Business Card

Company name: Larkspur Talent, Inc.
Website: www.larkspurtalent.example
Logos for Careerloop, Blipster, and Myriada

Name, Title, Office Number, Cell Number, email

Font styles to use
Serif
Sans Serif

Colors
0455a3
d5d5d5

Requirements
Nice to have
• The grey I selected below is not necessary - but, would like silver included. I included a card design (File 3: LTI early trial example.jpg) that I had started on. It's very rough, and not quite what we're looking for, but what we did like is the logo, big, maybe a bit faded, off center, goes out of frame, etc. Still looking for other ideas - you are the pros! But, just an idea of a design element we liked.

```html
<!DOCTYPE html>
<html lang="en">
<head>
<meta charset="utf-8">
<title>Larkspur Talent – Business Card</title>
<link rel="stylesheet" href="https://fonts.googleapis.com/css2?family=Cinzel:wght@400&family=Marcellus&family=Open+Sans:wght@400;600&display=swap">
<style>
  :root {
    --backdrop: #1b1b1b;
    --brand-blue: #0455a3;
    --band-light: #1a9ad9;
    --ink-grey: #555555;
    --paper: #ffffff;
    --back-grey: #575757;
    --faint-mark: #666666;
    --silver: #d5d5d5;
  }
  * { box-sizing: border-box; margin: 0; padding: 0; }
  html, body { width: 1200px; height: 907px; overflow: hidden; }
  body { background: var(--backdrop); position: relative; font-family: "Open Sans", Arial, sans-serif; }

  .card {
    position: absolute; left: 300px; width: 600px; height: 342px; overflow: hidden;
    box-shadow: 0 6px 18px rgba(0,0,0,.55);
  }
  .card--front { top: 98px; background: var(--paper); }
  .card--back { top: 475px; background: var(--back-grey); }

  /* wordmark */
  .wordmark { position: absolute; display: flex; align-items: center; gap: 12px; }
  .wordmark__dot { width: 40px; height: 40px; border-radius: 50%; flex: none; }
  .wordmark__text { display: flex; flex-direction: column; align-items: flex-end; font-family: "Cinzel", Georgia, serif; font-weight: 400; line-height: 1; }
  .wordmark__name { font-size: 34px; letter-spacing: 1px; }
  .wordmark__sub { font-size: 22px; letter-spacing: 3px; margin-top: 2px; }
  .wordmark__tagline { font-family: "Open Sans", Arial, sans-serif; font-size: 10px; font-weight: 600; letter-spacing: 1.2px; margin-top: 7px; text-transform: uppercase; }

  .card--front .wordmark { left: 50%; top: 42px; transform: translateX(-50%); color: var(--brand-blue); }
  .card--front .wordmark__dot { background: var(--brand-blue); }
  .card--front .wordmark__tagline { color: var(--ink-grey); }

  .person { position: absolute; top: 165px; width: 100%; text-align: center; font-family: "Marcellus", Georgia, serif; }
  .person__name { font-size: 30px; color: var(--brand-blue); line-height: 1.1; }
  .person__title { font-size: 20px; color: var(--ink-grey); margin-top: 4px; }

  .contact-band {
    position: absolute; left: 0; bottom: 0; width: 100%; height: 87px;
    background: linear-gradient(to bottom, var(--band-light), var(--brand-blue));
    color: var(--paper); font-size: 14px;
  }
  .contact-list { position: absolute; top: 19px; list-style: none; line-height: 25px; }
  .contact-list--left { left: 28px; }
  .contact-list--right { right: 26px; text-align: right; font-size: 13px; }
  .contact-list li { display: flex; align-items: center; gap: 8px; white-space: nowrap; }
  .contact-list--right li { justify-content: flex-end; }
  .contact-list svg { width: 13px; height: 13px; flex: none; }
  .band-disc { position: absolute; left: 255px; top: 6px; width: 90px; height: 90px; border-radius: 50%; background: var(--paper); }

  /* back */
  .back-mark { position: absolute; left: -10px; top: 0; width: 350px; height: 350px; border-radius: 50%; background: var(--faint-mark); }
  .social { position: absolute; right: 34px; top: 32px; display: flex; gap: 12px; list-style: none; color: var(--silver); font-size: 12px; }
  .social li { display: flex; align-items: center; gap: 5px; }
  .social__square { width: 14px; height: 14px; background: var(--brand-blue); border-radius: 2px; }
  .card--back .wordmark { right: 34px; bottom: 34px; color: var(--paper); }
  .card--back .wordmark__dot { background: var(--paper); }
  .card--back .wordmark__tagline { color: var(--silver); }
</style>
</head>
<body>

<section class="card card--front" aria-label="Business card front">
  <div class="wordmark">
    <span class="wordmark__dot"></span>
    <div class="wordmark__text">
      <span class="wordmark__name">LARKSPUR</span>
      <span class="wordmark__sub">TALENT</span>
      <span class="wordmark__tagline">IT Recruiting &amp; Contracting</span>
    </div>
  </div>

  <div class="person">
    <p class="person__name">Dana Whitfield</p>
    <p class="person__title">Manager</p>
  </div>

  <div class="contact-band">
    <ul class="contact-list contact-list--left">
      <li>
        <svg viewBox="0 0 16 16" aria-hidden="true"><path fill="currentColor" d="M4 1l3 3-2 2c1 2 3 4 5 5l2-2 3 3-2 3C7 14 2 9 1 3z"/></svg>
        555-014-2277
      </li>
      <li>
        <svg viewBox="0 0 16 16" aria-hidden="true"><rect x="4" y="1" width="8" height="14" rx="1.5" fill="currentColor"/><rect x="5.5" y="3" width="5" height="6" fill="var(--brand-blue)"/></svg>
        555-019-4830
      </li>
    </ul>

    <span class="band-disc"></span>

    <ul class="contact-list contact-list--right">
      <li>
        info@larkspurtalent.example
        <svg viewBox="0 0 16 16" aria-hidden="true"><rect x="1" y="3" width="14" height="10" fill="currentColor"/><path d="M1 3l7 6 7-6" fill="none" stroke="var(--brand-blue)" stroke-width="1.2"/></svg>
      </li>
      <li>
        www.larkspurtalent.example
        <svg viewBox="0 0 16 16" aria-hidden="true"><g fill="none" stroke="currentColor" stroke-width="1.2"><circle cx="8" cy="8" r="6.5"/><ellipse cx="8" cy="8" rx="3" ry="6.5"/><path d="M1.5 8h13"/></g></svg>
      </li>
    </ul>
  </div>
</section>

<section class="card card--back" aria-label="Business card back">
  <span class="back-mark"></span>

  <ul class="social">
    <li><span class="social__square"></span>Careerloop</li>
    <li><span class="social__square"></span>Blipster</li>
    <li><span class="social__square"></span>Myriada</li>
  </ul>

  <div class="wordmark">
    <span class="wordmark__dot"></span>
    <div class="wordmark__text">
      <span class="wordmark__name">LARKSPUR</span>
      <span class="wordmark__sub">TALENT</span>
      <span class="wordmark__tagline">IT Recruiting &amp; Contracting</span>
    </div>
  </div>
</section>

</body>
</html>
```